Quorva - corporate Business Card

We need a good look and innovative business card for a new start up company based in Los Angeles called "Quorva". We are in a payment business, including payment card, app, and ewallet. We are expert in online payment and Card not present (CNP) transaction.
We need an innovative, modern business card.

Our logo font is Aero Matics

Target Market(s)

Startup - Bank - Online Payment - Card Manufacturing

Industry/Entity Type

Startup

Contact Information for Business Card

phone: 555 014 7396 - Address: 4172 Marlowe blvd, Dunmere Park, NV 89163

Requirements
Must have
• Message: innovative, professional, expert, high tech, trust, online payment expert, security
Nice to have
• no comment
Should not have
• no Comment

```html
<!DOCTYPE html>
<html lang="en">
<head>
<meta charset="utf-8">
<title>Quorva — Business Card</title>
<link rel="stylesheet" href="https://fonts.googleapis.com/css2?family=Saira:wght@600&family=Open+Sans:wght@400;700&display=swap">
<style>
  :root {
    --stage: #3a3532;
    --brand-red: #b71f2e;
    --brand-red-deep: #a91c2a;
    --card-white: #ffffff;
    --blush: #f5e4df;
    --ink-grey: #8a8a8a;
  }
  * { margin: 0; padding: 0; box-sizing: border-box; }
  html, body { width: 1200px; height: 780px; overflow: hidden; }
  body {
    background: var(--stage);
    position: relative;
    font-family: "Open Sans", Arial, sans-serif;
  }
  .card {
    position: absolute;
    top: 240px;
    width: 525px;
    height: 300px;
    overflow: hidden;
    border-radius: 2px;
    box-shadow: 0 12px 30px rgba(0,0,0,.45);
  }
  .card-front { left: 60px; background: var(--brand-red); }
  .card-back  { left: 615px; background: var(--card-white); }

  .deco-circle {
    position: absolute;
    border-radius: 50%;
  }
  .card-front .deco-circle {
    width: 230px; height: 230px;
    right: 40px; top: 35px;
    background: var(--brand-red-deep);
  }
  .card-back .deco-circle {
    width: 300px; height: 300px;
    right: -95px; top: 40px;
    background: var(--blush);
  }

  .wordmark {
    font-family: "Saira", Arial, sans-serif;
    font-weight: 600;
    line-height: 1;
    letter-spacing: 1px;
    text-transform: lowercase;
  }
  .front-brand {
    position: absolute;
    left: 40px; top: 118px;
    display: flex; align-items: center; gap: 8px;
  }
  .brand-dot {
    width: 58px; height: 58px;
    border-radius: 50%;
    background: var(--card-white);
  }
  .front-brand .wordmark { color: var(--card-white); font-size: 52px; }

  .back-content {
    position: absolute;
    left: 36px; top: 62px;
  }
  .back-content .wordmark { color: var(--brand-red); font-size: 54px; }
  .person-name {
    margin-top: 18px;
    color: var(--brand-red);
    font-weight: 700;
    font-size: 17px;
  }
  .person-title {
    color: var(--ink-grey);
    font-size: 14px;
    margin-top: 1px;
  }
  .contact-line {
    display: flex; align-items: center; gap: 8px;
    color: var(--ink-grey);
    font-size: 13px;
    margin-top: 12px;
  }
  .contact-line + .contact-line { margin-top: 4px; }
  .phone-icon { width: 16px; height: 16px; flex: none; }
</style>
</head>
<body>
  <section class="card card-front" aria-label="Card front">
    <div class="deco-circle"></div>
    <div class="front-brand">
      <div class="brand-dot"></div>
      <span class="wordmark">quorva</span>
    </div>
  </section>

  <section class="card card-back" aria-label="Card back">
    <div class="deco-circle"></div>
    <div class="back-content">
      <div class="wordmark">quorva</div>
      <p class="person-name">Dorian Vale</p>
      <p class="person-title">Managing Director</p>
      <p class="contact-line">
        <svg class="phone-icon" viewBox="0 0 16 16" aria-hidden="true">
          <circle cx="8" cy="8" r="8" fill="#b71f2e"/>
          <path d="M5.2 4.2l1.4-.3.8 1.9-.9.7c.4.9 1.1 1.6 2 2l.7-.9 1.9.8-.3 1.4c-3.2.3-5.9-2.4-5.6-5.6z" fill="#fff"/>
        </svg>
        555 014 7396
      </p>
      <p class="contact-line">4172 Marlowe blvd, Dunmere Park, NV 89163</p>
    </div>
  </section>
</body>
</html>
```